Business Card Design Project

We are not a new company, but renamed to "Vantorin Kitchens" last year. We specialize in modern high-end cabinetry imports. We would like to communicate a sense of quality and cutting edge technology. Ideally the design would incorporate our logo colors, silver, red and preferably a black, matte background. Though we are open to suggestions.
Logo is attached.
Edit: I have attached rough drafts of the previous cards, this way you will have all necessary content that needs to go on the cards.
Updates
Project Deadline Extended
Reason: We have received a lot of great designs, but due to the sheer number we couldn't respond to all. We will extend the deadline for another 7 days to finalize and provide feedback to designers.
Thank you for your hard work!
Industry/Entity Type
Business
Look and feel
Each slider illustrates characteristics of the customer's brand and the style your logo design should communicate.

```html
<!DOCTYPE html>
<html lang="en">
<head>
<meta charset="utf-8">
<title>Vantorin Kitchens – Business Cards</title>
<link rel="stylesheet" href="https://fonts.googleapis.com/css2?family=Arimo:wght@400;700&display=swap">
<style>
  :root {
    --backdrop: #a9744a;
    --label: #2a1a10;
    --card-black: #141414;
    --card-black-2: #262626;
    --silver-light: #ececec;
    --silver-dark: #9a9a9a;
    --brand-red: #e0202a;
    --name-ink: #1a1a1a;
    --wordmark: #b9b9b9;
    --contact: #f2f2f2;
  }
  * { box-sizing: border-box; margin: 0; padding: 0; }
  html, body { width: 1200px; height: 788px; overflow: hidden; }
  body {
    background: var(--backdrop);
    font-family: "Arimo", Arial, sans-serif;
    position: relative;
  }
  .sheet-label {
    position: absolute;
    width: 300px;
    text-align: center;
    font-size: 21px;
    color: var(--label);
  }
  .card {
    position: absolute;
    width: 525px;
    height: 300px;
    border-radius: 20px;
    overflow: hidden;
    background: radial-gradient(ellipse at 50% 55%, var(--card-black-2), var(--card-black) 75%);
    box-shadow: 0 4px 10px rgba(0,0,0,0.35);
  }
  .card svg.card-art { position: absolute; inset: 0; }
  .holder { position: absolute; right: 16px; top: 26px; text-align: right; color: var(--name-ink); }
  .holder-name { font-size: 17px; font-weight: 700; letter-spacing: 0.3px; }
  .holder-title { font-size: 14px; margin-top: 3px; }
  .wordmark {
    position: absolute;
    color: var(--wordmark);
    font-weight: 700;
    text-transform: uppercase;
    white-space: nowrap;
  }
  .card-front .wordmark { left: 24px; top: 166px; font-size: 23px; letter-spacing: 1.5px; }
  .card-back .wordmark { left: 0; right: 0; top: 160px; text-align: center; font-size: 31px; letter-spacing: 2px; }
  .contact { position: absolute; right: 16px; top: 196px; text-align: right; color: var(--contact); font-size: 13px; line-height: 21px; }
  .contact b { font-weight: 700; }
  .address { position: absolute; left: 23px; bottom: 20px; color: var(--contact); font-size: 13px; }
  .email { position: absolute; right: 16px; bottom: 20px; color: var(--contact); font-size: 13px; }
  .perforation { position: absolute; }
</style>
</head>
<body>

<div class="sheet-label" style="left:156px; top:24px;">front</div>
<div class="sheet-label" style="left:732px; top:24px;">front-1</div>
<div class="sheet-label" style="left:165px; top:404px;">back</div>
<div class="sheet-label" style="left:730px; top:404px;">Back - 1</div>

<svg width="0" height="0" style="position:absolute">
  <defs>
    <linearGradient id="silverBand" x1="0" y1="0" x2="0" y2="1">
      <stop offset="0" stop-color="#8e8e8e"/>
      <stop offset="0.5" stop-color="#dcdcdc"/>
      <stop offset="1" stop-color="#f3f3f3"/>
    </linearGradient>
    <linearGradient id="redBand" x1="0" y1="0" x2="1" y2="0">
      <stop offset="0" stop-color="#c8101a"/>
      <stop offset="0.5" stop-color="#ee2a2f"/>
      <stop offset="1" stop-color="#c8101a"/>
    </linearGradient>
    <radialGradient id="perfGlow" cx="0.5" cy="0.5" r="0.5">
      <stop offset="0" stop-color="#6e6e6e"/>
      <stop offset="1" stop-color="#0d0d0d" stop-opacity="0"/>
    </radialGradient>
  </defs>
</svg>

<!-- Front: President -->
<div class="card card-front" style="left:53px; top:70px;">
  <svg class="card-art" viewBox="0 0 525 300" width="525" height="300" aria-hidden="true">
    <path d="M0,48 C60,36 130,36 210,60 C300,88 420,96 525,82 V96 C420,104 300,100 205,76 C130,58 60,58 0,68 Z" fill="url(#redBand)"/>
    <path d="M0,68 C60,58 130,58 205,76 C300,100 420,104 525,96 V100 C420,108 300,104 205,80 C130,62 60,62 0,72 Z" fill="#050505"/>
    <path d="M0,0 H525 V82 C420,96 300,88 210,60 C130,36 60,36 0,48 Z" fill="url(#silverBand)"/>
  </svg>
  <div class="holder">
    <div class="holder-name">MAREN OSTROV</div>
    <div class="holder-title">President</div>
  </div>
  <div class="wordmark">Vantorin Kitchens</div>
  <div class="contact">
    <div><b>p</b> : 555.201.0148</div>
    <div><b>c</b> : 555.201.3362</div>
    <div><b>f</b> : 555.201.0175</div>
  </div>
  <div class="address">2186 - 41 Ave., Larkfield, AB T4K 2M9</div>
  <div class="email"><b>e</b> : maren@vantorinkitchens.ca</div>
</div>

<!-- Front: Director -->
<div class="card card-front" style="left:620px; top:70px;">
  <svg class="card-art" viewBox="0 0 525 300" width="525" height="300" aria-hidden="true">
    <path d="M0,48 C60,36 130,36 210,60 C300,88 420,96 525,82 V96 C420,104 300,100 205,76 C130,58 60,58 0,68 Z" fill="url(#redBand)"/>
    <path d="M0,68 C60,58 130,58 205,76 C300,100 420,104 525,96 V100 C420,108 300,104 205,80 C130,62 60,62 0,72 Z" fill="#050505"/>
    <path d="M0,0 H525 V82 C420,96 300,88 210,60 C130,36 60,36 0,48 Z" fill="url(#silverBand)"/>
  </svg>
  <div class="holder">
    <div class="holder-name" style="font-weight:400;">TOBIAS OSTROV</div>
    <div class="holder-title" style="font-size:13px;">Director</div>
  </div>
  <div class="wordmark">Vantorin Kitchens</div>
  <div class="contact">
    <div><b>p</b> : 555.201.0148</div>
    <div><b>c</b> : 555.201.4490</div>
    <div><b>f</b> : 555.201.0175</div>
  </div>
  <div class="address">2186 - 41 Ave., Larkfield, AB T4K 2M9</div>
  <div class="email">e : tobias@vantorinkitchens.ca</div>
</div>

<!-- Back -->
<div class="card card-back" style="left:56px; top:446px;">
  <div class="wordmark">Vantorin Kitchens</div>
</div>

<!-- Back - 1 -->
<div class="card card-back" style="left:625px; top:446px; background:#0b0b0b;">
  <svg class="perforation" style="left:0; top:0;" width="280" height="110" viewBox="0 0 280 110" role="img" aria-label="Perforated metal texture, top left corner">
    <ellipse cx="150" cy="20" rx="150" ry="70" fill="url(#perfGlow)"/>
  </svg>
  <svg class="perforation" style="right:0; bottom:0;" width="260" height="110" viewBox="0 0 260 110" role="img" aria-label="Perforated metal texture, bottom right corner">
    <ellipse cx="110" cy="95" rx="140" ry="70" fill="url(#perfGlow)"/>
  </svg>
  <div class="wordmark" style="top:168px;">Vantorin Kitchens</div>
</div>

</body>
</html>
```